KRWB new business card design

We need a business card design for our established business which is Australia wide however based in Melbourne. We are a young team of Financial Planners who specialize in Insurance and Basic super advice for people like us.

We are people who help our clients get things done in a timely and cost effective manner whilst having a good time and a laugh along the way.

We would like this to have a consistent feel with our new e-brochure which i have attached from a color and font perspective.

Industry/Entity Type

Business

Requirements
Must have
• We do not need specific address details rather just the states we are in:

VIC/NSW/QLD/TAS
Nice to have
• Curved edge to mate the brochure

```html
<!DOCTYPE html>
<html lang="en">
<head>
<meta charset="utf-8">
<title>KRWB business card</title>
<link rel="stylesheet" href="https://fonts.googleapis.com/css2?family=Arimo:wght@400;700&display=swap">
<style>
  :root {
    --page: #e9e9e6;
    --card: #1b201d;
    --card-deep: #141815;
    --green: #5fae57;
    --lime: #9ccf4a;
    --white: #ffffff;
    --muted: #c9cec9;
    --photo-light: #9a9a9a;
    --photo-dark: #2a2a2a;
  }
  * { margin: 0; padding: 0; box-sizing: border-box; }
  html, body {
    width: 1200px;
    height: 900px;
    overflow: hidden;
    background: var(--page);
    font-family: "Arimo", Arial, sans-serif;
  }
  .sheet {
    position: relative;
    width: 1200px;
    height: 900px;
    display: flex;
    flex-direction: column;
    align-items: center;
    justify-content: center;
    gap: 40px;
  }
  .card {
    position: relative;
    width: 700px;
    height: 400px;
    border-radius: 4px;
    overflow: hidden;
    background: linear-gradient(135deg, var(--card) 0%, var(--card-deep) 100%);
    box-shadow: 0 6px 18px rgba(0,0,0,0.25);
    color: var(--white);
  }

  /* Front */
  .front-brand {
    position: absolute;
    left: 70px;
    top: 150px;
    display: flex;
    align-items: center;
    gap: 18px;
  }
  .brand-square {
    display: block;
    width: 70px;
    height: 70px;
    border-radius: 12px;
    background: var(--lime);
  }
  .brand-name {
    font-weight: 700;
    font-size: 34px;
    line-height: 1.05;
    color: var(--white);
  }
  .front-photo {
    position: absolute;
    right: 0;
    top: 0;
    width: 230px;
    height: 400px;
  }

  /* Back */
  .back-brand {
    position: absolute;
    left: 52px;
    top: 104px;
    width: 140px;
    display: flex;
    flex-direction: column;
    align-items: flex-start;
    gap: 10px;
  }
  .back-brand .brand-square {
    width: 52px;
    height: 52px;
    border-radius: 9px;
  }
  .back-brand .brand-name {
    font-size: 18px;
    line-height: 1.1;
  }
  .tagline {
    position: absolute;
    left: 210px;
    top: 106px;
    font-weight: 700;
    font-size: 22px;
    line-height: 1.2;
    letter-spacing: 0.3px;
    text-transform: uppercase;
  }
  .states {
    position: absolute;
    right: 40px;
    top: 96px;
    list-style: none;
    text-align: right;
    font-size: 15px;
    line-height: 1.3;
    color: var(--muted);
    text-transform: uppercase;
  }
  .contact {
    position: absolute;
    left: 52px;
    bottom: 40px;
    font-size: 16px;
    font-style: normal;
    line-height: 1.35;
  }
</style>
</head>
<body>
<main class="sheet">

  <section class="card card-front">
    <div class="front-brand">
      <span class="brand-square"></span>
      <span class="brand-name">Kestrel Ridge<br>Wealth</span>
    </div>
    <svg class="front-photo" viewBox="0 0 230 400">
      <defs>
        <linearGradient id="photoTone" x1="0" y1="0" x2="1" y2="1">
          <stop offset="0" stop-color="#9a9a9a"/>
          <stop offset="1" stop-color="#2a2a2a"/>
        </linearGradient>
      </defs>
      <path d="M0 0 H230 V400 H58 C58 330 70 290 40 250 C15 215 18 60 0 0 Z" fill="#5fae57"/>
      <path role="img" aria-label="Black and white portrait photo of a smiling team member"
            d="M14 0 H230 V400 H72 C72 330 84 290 54 250 C30 215 32 60 14 0 Z" fill="url(#photoTone)"/>
    </svg>
  </section>

  <section class="card card-back">
    <div class="back-brand">
      <span class="brand-square"></span>
      <span class="brand-name">Kestrel Ridge<br>Wealth</span>
    </div>
    <h2 class="tagline">Secure future,<br>enhanced lifestyle</h2>
    <ul class="states">
      <li>Tasmania</li>
      <li>Victoria</li>
      <li>Gold Coast</li>
      <li>New South Wales</li>
    </ul>
    <address class="contact">
      1300 555 014<br>
      admin@krwb.com.au<br>
      www.kestrelridgewealth.com.au
    </address>
  </section>

</main>
</body>
</html>
```